VORLAND COMPOSITES INC website in USA

VORLAND COMPOSITES INC incorporated and operated in USA needs a completely new design of website. This Wyoming based company is a importer and distributor of composites material to supply mainly to American and Canadian/Mexican customers. Our main products includes Carbon Fiber, Aramid Fiber, Glass Fiber, Basalt Fiber, High Silica Glass, Quartz Fiber, S-Glass, Alumina Fiber, Vacuum Auxiliary.

We are one stop composites solution provider for Automotive, Aerospace, Construction, Electrical and Machinery industries.

We are exclusive sales company in North America for BLORAN composites produced from China and their other Asia facilities.

Target Market(s)

USA and Canada

Industry/Entity Type

Composites materials

Coding

Coded - Design and coding required

Number of Pages Required

5+ page

Requirements
Nice to have
• Color theme to match our corporate logo VORLAND. VORLAND stands for Northgate Provisioning Trade Holdings

```html
<!DOCTYPE html>
<html lang="en">
<head>
<meta charset="utf-8">
<title>Vorland Composites Inc</title>
<link href="https://fonts.googleapis.com/css2?family=Montserrat:wght@600;700;800&family=Open+Sans:wght@400;600;700&display=swap" rel="stylesheet">
<style>
:root{
  --orange:#f29125;
  --orange-dark:#e2801a;
  --ink:#1f1f1f;
  --text:#555;
  --grey-bg:#f4f4f4;
  --footer:#3a3a3a;
  --white:#fff;
}
*{margin:0;padding:0;box-sizing:border-box}
html,body{width:1200px;height:2990px;overflow:hidden}
body{font-family:"Open Sans",sans-serif;color:var(--text);background:var(--white);position:relative}
.abs{position:absolute}
h1,h2,h3{font-family:"Montserrat",sans-serif;font-weight:800}
.btn{position:absolute;background:var(--orange);color:#fff;font-family:"Open Sans",sans-serif;font-weight:700;font-size:15px;display:flex;align-items:center;justify-content:center;border-radius:3px;letter-spacing:.3px}
.star{color:var(--orange);font-size:26px;position:absolute;font-family:sans-serif}

/* header */
.site-header{position:absolute;top:0;left:0;width:1200px;height:78px;background:#fff}
.brand{position:absolute;left:144px;top:20px;display:flex;align-items:center;gap:12px}
.brand-name{font-family:"Open Sans",sans-serif;font-weight:700;font-size:30px;color:var(--orange);letter-spacing:-.5px}
.brand-rule{width:1px;height:44px;background:#999}
.brand-tag{font-size:8.5px;line-height:11px;color:#333;width:80px}
.nav{position:absolute;right:146px;top:30px;display:flex;gap:41px;font-size:14.5px;color:#222}
.nav .active{color:var(--orange)}

/* hero */
.hero{position:absolute;top:78px;left:0;width:1200px;height:560px;background:linear-gradient(100deg,#1b1c1e 0%,#2a2b2e 45%,#4a4a4c 70%,#2e2f31 100%)}
.hero-eyebrow{left:143px;top:182px;color:var(--orange);font-size:14.5px}
.hero-title{left:143px;top:218px;color:#fff;font-size:40px;line-height:52px;letter-spacing:.3px}
.hero-text{left:143px;top:381px;color:#fff;font-size:18px;line-height:29px}
.dots{left:576px;top:592px;display:flex;gap:7px}
.dots span{width:11px;height:11px;border-radius:50%;border:2px solid #fff}
.dots span.on{background:var(--orange);border-color:var(--orange)}

/* about */
.about-accent{left:130px;top:832px;width:366px;height:292px;background:var(--orange);clip-path:polygon(0 0,100% 100%,0 100%)}
.about-accent2{left:130px;top:1100px;width:366px;height:24px;background:var(--orange);clip-path:polygon(0 0,93% 0,100% 100%,0 100%)}
.about-photo{left:145px;top:718px;width:440px;height:394px;background:linear-gradient(120deg,#3a3f44,#6b6f70 45%,#2f4a7a 75%,#2b2d31)}
.about-title{left:649px;top:760px;font-size:37px;color:var(--ink)}
.about-text{left:649px;top:826px;width:400px;font-size:13.5px;line-height:24px;text-align:justify;color:#666}
.about-text p+p{margin-top:6px}

/* products */
.products{position:absolute;top:1207px;left:0;width:1200px;height:551px;background:var(--grey-bg)}
.sec-title{position:absolute;width:1200px;text-align:center;color:var(--ink);font-size:37px}
.sec-lead{position:absolute;left:150px;width:900px;text-align:center;font-size:16.5px;line-height:29px;color:#555}
.card{position:absolute;background:#fff;box-shadow:0 1px 4px rgba(0,0,0,.08)}
.card .pic{height:192px}
.card .label{height:47px;display:flex;align-items:center;justify-content:center;font-size:16.5px;color:#222}
.card.active{background:var(--orange)}
.card.active .label{color:#fff}
.arrow{position:absolute;top:1535px}

/* industries */
.industries{position:absolute;top:1758px;left:0;width:1200px;height:360px;background:var(--orange)}
.ind-card{position:absolute;top:1894px;width:177px;height:158px;background:#fff;text-align:center}
.ind-card svg{margin-top:22px}
.ind-card p{font-size:15.5px;color:#222;margin-top:14px}

/* cta */
.cta{position:absolute;top:2118px;left:0;width:1200px;height:406px;background:var(--grey-bg);overflow:hidden}
.mat{position:absolute}

/* footer */
.footer{position:absolute;top:2524px;left:0;width:1200px;height:466px;background:var(--footer);color:#fff}
.f-col{position:absolute;top:64px}
.f-title{font-family:"Montserrat",sans-serif;font-weight:600;font-size:16px;color:#fff;letter-spacing:.2px}
.f-title::after{content:"";display:block;width:56px;height:2px;background:var(--orange);margin-top:9px}
.f-list{list-style:none;margin-top:22px;font-size:14px;line-height:24px}
.f-list li::before{content:"»";color:var(--orange);margin-right:12px}
.f-label{font-size:14px;margin-top:20px;text-transform:uppercase}
.f-val{font-size:14px;line-height:24px;margin-top:4px;display:flex;gap:9px;align-items:flex-start}
.f-val svg{flex:none;margin-top:5px}
.f-rule{position:absolute;left:144px;top:348px;width:912px;height:1px;background:#5a5a5a}
.copy{position:absolute;top:366px;width:1200px;text-align:center;font-size:14px}
.social{position:absolute;top:402px;left:549px;display:flex;gap:8px}
.social span{width:28px;height:28px;border-radius:50%;border:1.5px solid var(--orange)}
.social span.on{background:var(--orange)}
</style>
</head>
<body>

<header class="site-header">
  <div class="brand">
    <span class="brand-name">VORLAND</span>
    <span class="brand-rule"></span>
    <span class="brand-tag">Northgate Provisioning Trade Holdings</span>
  </div>
  <nav class="nav">
    <span class="active">HOME</span><span>ABOUT</span><span>PRODUCTS</span><span>INDUSTRIES</span><span>BLOG</span><span>CONTACT</span>
  </nav>
</header>

<section class="hero" role="img" aria-label="Photo of a machine cutting woven carbon fibre sheets"></section>
<p class="abs hero-eyebrow">NORTHGATE PROVISIONING TRADE HOLDINGS</p>
<h1 class="abs hero-title">YOUR TRUSTED PARTNER<br>IN ADVANCED COMPOSITE<br>MATERIALS</h1>
<p class="abs hero-text">We Import and Distribute Premium-quality Composite Materials<br>For Industries That Demand Performance and Precision.</p>
<div class="btn" style="left:144px;top:476px;width:224px;height:47px">EXPLORE PRODUCTS</div>
<div class="abs dots"><span class="on"></span><span></span><span></span></div>

<div class="abs about-accent"></div>
<div class="abs about-accent2"></div>
<div class="abs about-photo" role="img" aria-label="Photo of two engineers in hard hats reviewing a clipboard beside a control panel"></div>
<h2 class="abs about-title">ABOUT US</h2>
<span class="star" style="left:851px;top:746px">★</span>
<div class="abs about-text">
  <p>Lorem ipsum dolor sit amet, consectetur adipiscing elit, sed do eiusmod tempor incididunt ut labore et dolore magna aliqua. Ut enim ad minim veniam, quis nostrud exercitation ullamco laboris nisi ut aliquip ex ea commodo consequat.</p>
  <p>Duis aute irure dolor in reprehenderit in voluptate velit esse cillum dolore eu fugiat nulla pariatur. Excepteur sint occaecat cupidatat non proident, sunt in culpa</p>
</div>
<div class="btn" style="left:649px;top:1033px;width:216px;height:43px">LEARN MORE ABOUT US</div>

<section class="products"></section>
<h2 class="sec-title" style="top:1270px">OUR PRODUCTS</h2>
<span class="star" style="left:757px;top:1256px">★</span>
<p class="sec-lead" style="top:1329px">Sed ut perspiciatis unde omnis iste natus error sit voluptatem accusantium doloremque laudantium, totam rem aperiam, eaque ipsa quae ab illo inventore veritatis et quasi architecto</p>

<svg class="arrow" style="left:110px" width="16" height="26" viewBox="0 0 16 26"><path d="M13 2 3 13l10 11" fill="none" stroke="#444" stroke-width="2.5"/></svg>
<svg class="arrow" style="left:1074px" width="16" height="26" viewBox="0 0 16 26"><path d="M3 2l10 11L3 24" fill="none" stroke="#444" stroke-width="2.5"/></svg>

<div class="card" style="left:145px;top:1432px;width:216px">
  <div class="pic" role="img" aria-label="Photo of woven carbon fibre fabric" style="background:linear-gradient(135deg,#111,#555 50%,#1a1a1a)"></div>
  <div class="label">Carbon Fiber</div>
</div>
<div class="card" style="left:367px;top:1432px;width:215px">
  <div class="pic" role="img" aria-label="Photo of golden aramid fibre strands" style="background:radial-gradient(circle at 50% 45%,#ffd35a,#d89a17 60%,#8a5a0b)"></div>
  <div class="label">Aramid Fiber</div>
</div>
<div class="card active" style="left:586px;top:1416px;width:248px">
  <div class="pic" role="img" aria-label="Photo of rolled basalt fibre fabric" style="height:224px;background:linear-gradient(135deg,#3a3430,#8b8178 50%,#2d2926)"></div>
  <div class="label">Basalt Fiber</div>
</div>
<div class="card" style="left:839px;top:1432px;width:216px">
  <div class="pic" role="img" aria-label="Photo of loose alumina fibre wool" style="background:linear-gradient(135deg,#d8d2c6,#b9b1a2 50%,#e6e1d8)"></div>
  <div class="label">Alumina Fiber</div>
</div>

<section class="industries"></section>
<h2 class="sec-title" style="top:1820px;color:#fff">INDUSTRIES WE SERVED</h2>
<span class="star" style="left:840px;top:1806px;color:#fff">★</span>

<div class="ind-card" style="left:144px">
  <svg width="76" height="80" viewBox="0 0 76 80" fill="none" stroke="#333" stroke-width="3"><circle cx="22" cy="12" r="6"/><path d="M22 18l-4 26M26 14l20 18M46 32l8-6M46 32l6 10"/><rect x="12" y="44" width="22" height="14" rx="3"/><path d="M8 72h34" stroke-width="4"/><path d="M18 58v14M28 58v14"/><circle cx="23" cy="68" r="3" stroke="var(--orange)"/></svg>
  <p>Automotive</p>
</div>
<div class="ind-card" style="left:328px">
  <svg width="76" height="80" viewBox="0 0 76 80" fill="none" stroke="#333" stroke-width="3"><circle cx="38" cy="38" r="26"/><circle cx="38" cy="38" r="14" stroke="var(--orange)"/><path d="M38 6v6M38 64v6M6 38h6M64 38h6M15 15l5 5M56 56l5 5M61 15l-5 5M15 61l5-5"/><path d="M20 74h36"/></svg>
  <p>Aerospace</p>
</div>
<div class="ind-card" style="left:512px">
  <svg width="86" height="80" viewBox="0 0 86 80" fill="none" stroke="#333" stroke-width="3"><circle cx="26" cy="34" r="14"/><circle cx="26" cy="34" r="5" stroke="var(--orange)"/><circle cx="56" cy="40" r="9"/><path d="M68 6v24M62 6v8h12V6"/><rect x="8" y="62" width="70" height="10" rx="5"/><path d="M16 67h40" stroke="var(--orange)"/></svg>
  <p>Machinery Industries</p>
</div>
<div class="ind-card" style="left:696px">
  <svg width="80" height="80" viewBox="0 0 80 80" fill="none" stroke="#333" stroke-width="3"><circle cx="40" cy="40" r="28"/><circle cx="40" cy="40" r="19"/><path d="M40 4v8M40 68v8M4 40h8M68 40h8M15 15l6 6M59 59l6 6M65 15l-6 6M15 65l6-6"/><path d="M44 26l-10 16h10l-6 14" stroke="var(--orange)"/></svg>
  <p>Electrical</p>
</div>
<div class="ind-card" style="left:879px">
  <svg width="76" height="80" viewBox="0 0 76 80" fill="none" stroke="#333" stroke-width="3"><path d="M24 28a14 14 0 0 1 28 0z"/><path d="M20 28h36"/><path d="M27 32a11 11 0 0 0 22 0"/><path d="M14 74V60c0-8 10-12 24-12s24 4 24 12v14"/><path d="M32 48l6 10 6-10"/><circle cx="20" cy="16" r="6" stroke="var(--orange)"/></svg>
  <p>Construction</p>
</div>

<section class="cta">
  <div class="mat" role="img" aria-label="Photo of loose fibre tufts" style="left:0;top:0;width:140px;height:140px;background:radial-gradient(circle at 20% 40%,#cdbb8e,rgba(205,187,142,0) 70%)"></div>
  <div class="mat" role="img" aria-label="Photo of stacked silica fabric sheets" style="left:1070px;top:0;width:130px;height:140px;background:radial-gradient(circle at 70% 50%,#e9e3d6,rgba(233,227,214,0) 70%)"></div>
  <div class="mat" role="img" aria-label="Photo of black fibre tape" style="left:0;top:254px;width:270px;height:152px;background:radial-gradient(ellipse at 30% 70%,#2a2d33,rgba(42,45,51,0) 70%)"></div>
  <div class="mat" role="img" aria-label="Photo of white mineral fibre lump" style="left:286px;top:290px;width:234px;height:116px;background:radial-gradient(ellipse at 50% 65%,#eeeeee,#cfcfcf 55%,rgba(207,207,207,0) 72%)"></div>
  <div class="mat" role="img" aria-label="Photo of stacked insulation boards" style="left:550px;top:296px;width:226px;height:110px;background:radial-gradient(ellipse at 50% 55%,#b79d63,#8d7644 55%,rgba(141,118,68,0) 72%)"></div>
  <div class="mat" role="img" aria-label="Photo of a coiled fibre bundle" style="left:800px;top:296px;width:170px;height:110px;background:radial-gradient(ellipse at 50% 60%,#8a7a62,rgba(138,122,98,0) 70%)"></div>
  <div class="mat" role="img" aria-label="Photo of a rolled green coated fabric" style="left:950px;top:188px;width:250px;height:218px;background:radial-gradient(ellipse at 50% 45%,#2c5a4a,#1e4236 55%,rgba(30,66,54,0) 72%)"></div>
</section>
<h2 class="sec-title" style="top:2184px;font-size:38px">TALK TO OUR MATERIALS EXPERTS TODAY</h2>
<span class="star" style="left:1013px;top:2170px">★</span>
<p class="sec-lead" style="top:2245px;left:140px;width:920px;font-size:14.5px;line-height:24px">Lorem ipsum dolor sit amet, consectetur adipiscing elit, sed do eiusmod tempor incididunt ut labore et dolore magna aliqua. Ut enim ad minim veniam, quis nostrud exercitation ullamco laboris nisi ut aliquip ex ea commodo consequat.</p>
<div class="btn" style="left:528px;top:2327px;width:143px;height:44px">CONTACT US</div>

<footer class="footer">
  <div class="f-col" style="left:144px">
    <div class="f-title">QUICK LINKS</div>
    <ul class="f-list"><li>Home</li><li>About Us</li><li>Products</li><li>Industries</li><li>Blog</li><li>Contact</li></ul>
  </div>
  <div class="f-col" style="left:308px">
    <div class="f-title">PRODUCT CATEGORIES</div>
    <ul class="f-list"><li>Carbon Fiber</li><li>Aramid Fiber</li><li>Glass Fiber</li><li>Basalt Fiber</li><li>High Silica Glass</li><li>Quartz Fiber</li><li>S-Glass,</li><li>Alumina Fiber</li><li>Vacuum Auxiliary</li></ul>
  </div>
  <div class="f-col" style="left:558px;width:240px">
    <div class="f-title">VORLAND COMPOSITES INC</div>
    <div class="f-label" style="margin-top:24px">Phone</div>
    <div class="f-val"><svg width="13" height="13" viewBox="0 0 24 24"><path fill="var(--orange)" d="M6.6 10.8a15 15 0 0 0 6.6 6.6l2.2-2.2c.3-.3.7-.4 1-.2 1.1.4 2.3.6 3.6.6.6 0 1 .4 1 1V20c0 .6-.4 1-1 1A17 17 0 0 1 3 4c0-.6.4-1 1-1h3.5c.6 0 1 .4 1 1 0 1.3.2 2.5.6 3.6.1.3 0 .7-.2 1z"/></svg>307-555-0148</div>
    <div class="f-label">Email Address</div>
    <div class="f-val"><svg width="14" height="11" viewBox="0 0 24 18"><rect width="24" height="18" rx="2" fill="var(--orange)"/><path d="M1 2l11 8 11-8" stroke="#3a3a3a" stroke-width="2" fill="none"/></svg>sales@vorlandcomposites.example</div>
    <div class="f-label">Location</div>
    <div class="f-val"><svg width="11" height="14" viewBox="0 0 16 22"><path fill="var(--orange)" d="M8 0a8 8 0 0 0-8 8c0 6 8 14 8 14s8-8 8-14a8 8 0 0 0-8-8zm0 11a3 3 0 1 1 0-6 3 3 0 0 1 0 6z"/></svg><span>214 Ridgeline Ave, Sheridan,<br>WY, USA 82800</span></div>
  </div>
  <div class="f-col" style="left:827px;width:240px">
    <div class="f-title">VORLAND INC</div>
    <div class="f-label" style="margin-top:24px">Phone</div>
    <div class="f-val"><svg width="13" height="13" viewBox="0 0 24 24"><path fill="var(--orange)" d="M6.6 10.8a15 15 0 0 0 6.6 6.6l2.2-2.2c.3-.3.7-.4 1-.2 1.1.4 2.3.6 3.6.6.6 0 1 .4 1 1V20c0 .6-.4 1-1 1A17 17 0 0 1 3 4c0-.6.4-1 1-1h3.5c.6 0 1 .4 1 1 0 1.3.2 2.5.6 3.6.1.3 0 .7-.2 1z"/></svg>416-555-0172</div>
    <div class="f-label">Email Address</div>
    <div class="f-val"><svg width="14" height="11" viewBox="0 0 24 18"><rect width="24" height="18" rx="2" fill="var(--orange)"/><path d="M1 2l11 8 11-8" stroke="#3a3a3a" stroke-width="2" fill="none"/></svg>sales@vorlandcomposites.example</div>
    <div class="f-label">Location</div>
    <div class="f-val"><svg width="11" height="14" viewBox="0 0 16 22"><path fill="var(--orange)" d="M8 0a8 8 0 0 0-8 8c0 6 8 14 8 14s8-8 8-14a8 8 0 0 0-8-8zm0 11a3 3 0 1 1 0-6 3 3 0 0 1 0 6z"/></svg><span>1180 Maple Crest Rd, Suite 300,<br>Markham, ON, L3R 0A0, Canada</span></div>
  </div>
  <div class="f-rule"></div>
  <p class="copy">© 2025 Copyright All Right Reserved. Vorland Composite Inc</p>
  <div class="social"><span></span><span class="on"></span><span></span></div>
</footer>

</body>
</html>
```